Human Resource Consulting practice needs a business card design

We need a business card design (double sided colour) for our Human Resource (HR) consulting practice in regional New South Wales, australia. Our business name is Staff Compass. We support small and medium business across the Mid North Coast of New South Wales by providing them with outsourced HR support, services and products to help them achieve compliance with workplace legislation and across all areas of the employment lifecycle from recruitment to termination and everything in between. Our corporate colours are hot pink and black. The final design should communicate professionalism, trust, people focus.
I have attached the current (old) business card for your reference.

Target Market(s)

Business owners and high level managers

Industry/Entity Type

Business

Contact Information for Business Card

Name
Title
Phone no
Mobile no
Address
PO Box
email address
website

Colors
e34197

Requirements
Must have
• Tempate for changing business card personal details including Name, position title, mobile number, email address.
• Keep current logo and colours as per attached
• Logo must be presented in 2 colours or black only not white
Nice to have
• One side logo and graphic only other side logo and personal details
Should not have
• Should not be the same as the current version (attached) but a modern interpretation.
• Does not need a busy reverse side with our list of services as per current version. I feel this is too busy.
• No photos

```html
<!DOCTYPE html>
<html lang="en">
<head>
<meta charset="utf-8">
<title>Staff Compass – Business Card</title>
<link rel="stylesheet" href="https://fonts.googleapis.com/css2?family=Archivo:wght@400;500;800&display=swap">
<style>
  :root {
    --pink: #e4138b;
    --ink: #1a1a1a;
    --paper: #ffffff;
    --stage: #e9e6e3;
    --star-grey: #d9dadc;
  }
  * { box-sizing: border-box; margin: 0; padding: 0; }
  html, body {
    width: 1200px; height: 1189px; overflow: hidden;
    background: var(--stage);
    font-family: "Archivo", Arial, sans-serif;
  }
  .sheet {
    width: 1200px; height: 1189px;
    display: flex; flex-direction: column; align-items: center;
    justify-content: center; gap: 56px;
  }
  .card {
    position: relative;
    width: 860px; height: 526px;
    background: var(--paper);
    box-shadow: 0 6px 22px rgba(0,0,0,0.12);
    overflow: hidden;
  }
  .wordmark {
    font-family: "Archivo", Arial, sans-serif;
    font-weight: 800;
    color: var(--pink);
    letter-spacing: -0.5px;
    white-space: nowrap;
    display: flex; align-items: center; gap: 12px;
  }
  .wordmark-dot {
    width: 12px; height: 12px; background: var(--pink);
  }

  /* Reverse side */
  .card--reverse .pattern-area {
    position: absolute; top: 0; right: 0;
    width: 470px; height: 250px;
    background: linear-gradient(200deg, var(--star-grey) 0%, #eceded 55%, var(--paper) 100%);
  }
  .card--reverse .wordmark {
    position: absolute; left: 150px; top: 320px;
    font-size: 66px;
  }

  /* Front side */
  .card--front .wordmark {
    position: absolute; left: 70px; top: 210px;
    font-size: 50px;
  }
  .divider {
    position: absolute; left: 455px; top: 95px;
    width: 2px; height: 290px; background: var(--pink);
  }
  .person {
    position: absolute; left: 488px; top: 100px;
  }
  .person-name {
    font-weight: 800; font-size: 30px; color: var(--pink); line-height: 1;
  }
  .person-title {
    font-weight: 500; font-size: 14px; color: var(--ink);
    letter-spacing: 0.6px; text-transform: uppercase; margin-top: 5px;
  }
  .contact-list {
    position: absolute; left: 488px; top: 190px;
    list-style: none;
  }
  .contact-list li {
    display: flex; align-items: center; gap: 12px;
    font-size: 19px; color: var(--ink); line-height: 1; height: 32px;
    letter-spacing: 0.3px;
  }
  .contact-icon {
    width: 22px; height: 22px; flex: none;
  }
  .address-band {
    position: absolute; left: 0; right: 0; bottom: 0; height: 90px;
    background: var(--pink);
    display: flex; align-items: center; justify-content: center;
    color: var(--paper); font-size: 26px; letter-spacing: 1px;
  }
</style>
</head>
<body>
<main class="sheet">

  <section class="card card--reverse" aria-label="Card reverse side">
    <div class="pattern-area" role="img" aria-label="Scattered light grey star pattern"></div>
    <div class="wordmark"><span class="wordmark-dot"></span>Staff Compass</div>
  </section>

  <section class="card card--front" aria-label="Card front side">
    <div class="wordmark"><span class="wordmark-dot"></span>Staff Compass</div>
    <div class="divider"></div>
    <div class="person">
      <p class="person-name">Megan Hale</p>
      <p class="person-title">Principal Consultant</p>
    </div>
    <ul class="contact-list">
      <li>
        <svg class="contact-icon" viewBox="0 0 22 22" aria-hidden="true">
          <rect width="22" height="22" rx="4" fill="var(--pink)"/>
          <path d="M6 6.5c1-1 2-1 2.6 0l1 1.6c.4.6.2 1.2-.4 1.6l-.6.4c.6 1.5 1.6 2.6 3.2 3.3l.5-.6c.4-.6 1-.8 1.6-.4l1.6 1c1 .6 1 1.6 0 2.5-3.6 2.6-11.8-5.6-9.5-9.4z" fill="#fff"/>
        </svg>
        02 6500 1234
      </li>
      <li>
        <svg class="contact-icon" viewBox="0 0 22 22" aria-hidden="true">
          <rect width="22" height="22" rx="4" fill="var(--pink)"/>
          <rect x="7.5" y="4" width="7" height="14" rx="1.5" fill="#fff"/>
          <rect x="8.8" y="6" width="4.4" height="8" fill="var(--pink)"/>
        </svg>
        0400 555 812
      </li>
      <li>
        <svg class="contact-icon" viewBox="0 0 22 22" aria-hidden="true">
          <rect width="22" height="22" rx="4" fill="var(--pink)"/>
          <rect x="4.5" y="6.5" width="13" height="9" fill="#fff"/>
          <path d="M4.5 6.5 11 12l6.5-5.5" fill="none" stroke="var(--pink)" stroke-width="1.3"/>
        </svg>
        megan@staffcompass.com.au
      </li>
      <li>
        <svg class="contact-icon" viewBox="0 0 22 22" aria-hidden="true">
          <rect width="22" height="22" rx="4" fill="var(--pink)"/>
          <circle cx="11" cy="11" r="6" fill="none" stroke="#fff" stroke-width="1.4"/>
          <ellipse cx="11" cy="11" rx="2.6" ry="6" fill="none" stroke="#fff" stroke-width="1.2"/>
          <path d="M5 11h12" stroke="#fff" stroke-width="1.2"/>
        </svg>
        www.staffcompass.com.au
      </li>
    </ul>
    <div class="address-band">P.O. Box 218 Harbour Point, NSW 2400</div>
  </section>

</main>
</body>
</html>
```